IT Company needs Website for new Web and Mobile products for Sports and Fitness

Background:

We developed web based white label frontend web solution, backend services and white label mobile apps for to log, analyze, share and control sport and fitness activities. The name of this product suite is "Trevantix" (http://trevantix-example.com)

This products will be used by customers that provide platforms and community systems for sport and fitness. One of the major USP's is, that our technology i open for nearly all common formats, devices and apps out in the market. This means, you can just upload your data directly from device, file or app - e.G. Kestrel, Bolvane, Ravelo, StrideVault, Pacelumo, Zembra and much others.

Two current concrete examples/References

(1) MyQuorel
It's an international platform from quorel for runners. It provides individual training lans and a training log. MyQuorel uses the Backend Product "Trevantix Hub" (see http://hub.trevantix-example.net for a landing page) to integrate device, file and app support. Before this, every user has to track his training with manual inputs

(2) Paceharbor and fen-zine
Both are German customers. Paceharor is focused on runners. fen-zine is focused on Triatheletes. Both use the Product "Trevantix Web". This is a complete web solution with web based frontend solutions for athletes and coaches.

What do we need?
We need website layout for B2B for our products. We don't need lot's of pages. We need the pretty and nice layout, so we can derive the pages we need.

IMPORTANT
We don't talk about the webpages for the product itself (this will be a different project in future). We talk about a website, explaining the products)
Updates

Hi all,

we just start reviewing the first designs, and try to give feedback as detailed as possible. We attached a PDF document, to describe the the products a little bit more detailed. 

As written in the description, in the end we have two different sections. One is the usual stuff like "start page", "about", "contact", "disclaimer", "pricing", "blah...." and one will be the Developer Section, the "Tec Section". This ist aimed to developers (of our customers) that will integrate our products in there existing system or which will integrate our services in there own software.  This "pages" are more like "documentation", so easy to read and cool to look at (cause developers likes it cool, but straight)

Dear all,

we just do the final review. Cause this week is with heavy load, it takes some time...

Cheers

Odell

Target Market(s)

* Platforms and Communities for sport, health and fitness
* Gyms

Industry/Entity Type

Concrete

Font styles to use
Sans Serif

Requirements
Must have
• * Templates shall base on bootstrap. If not, it shall be easily realized on our site with bootstrap or out of the box "full responsive"

* HTML5 / CSS3
Nice to have
• PAGES
- Start Page
- Generic Template (from which we can derive additional pages)
- Contact Page
- Disclaimer Page
- Blog/News Page
- "About us" Page (can be combined with disclaimer)
- One Example product page (in end we have 3 products), shall show (if you need product details, let me know)
- product and it's description
- pricing information
- Add-Ons for the product
- Developer Section Page (Start Point for developers, where the finde "basic technical concepts and developer API's
- Example Developer Page for technical concept
- Example Developer Page for API

LOGO ISSUE
You can use an align to the Logo attached OR provide a new logo. The given logo is a logo for our own B2C Website http://trevantix-example.net. It's not really necessary, that the logo or the color must be used for the product website. Maybe it will be better if it's a complete new one, to avoid irritation between Trevantix as a B2B product and trevantix-example.net as a B2C platform.
Should not have
• No Flash and other proprietary technologies

```html
<!DOCTYPE html>
<html lang="en">
<head>
<meta charset="utf-8">
<title>Trevantix – Web and Mobile Solutions for Sport</title>
<link rel="stylesheet" href="https://fonts.googleapis.com/css2?family=Raleway:wght@400;500;600;700&family=Archivo+Black&family=Arimo:wght@400;700&display=swap">
<style>
:root{
  --orange:#e8740c;
  --orange-soft:#f2a65e;
  --olive-dark:#5b4a0b;
  --olive:#a88f2b;
  --olive-light:#cbb85c;
  --ink:#444;
  --white:#fff;
  --black:#000;
}
*{box-sizing:border-box;margin:0;padding:0}
html,body{width:850px;height:1200px;overflow:hidden}
body{position:relative;font-family:"Raleway",sans-serif;color:var(--ink);background:var(--white)}
.abs{position:absolute}

/* top bar */
.topbar{left:0;top:0;width:850px;height:29px;background:var(--orange);color:var(--white);font-size:8px}
.topbar .links{left:26px;top:9px}
.topbar .mail{left:240px;top:9px}
.topbar .mail i{display:inline-block;width:18px;height:11px;border:1.5px solid var(--white);vertical-align:-2px;margin-right:4px}
.topbar .search{left:548px;top:9px;width:128px;height:13px;background:var(--white);font-size:7px;color:#ccc;padding:2px 4px}
.topbar .social{left:714px;top:7px;display:flex;gap:3px}
.dot{width:16px;height:16px;border-radius:50%;background:#3a9ad6}
.dot.b{background:#3b5998}.dot.c{background:#555}

/* header */
.brand{left:10px;top:40px;display:flex;align-items:center;gap:6px;font-size:26px;font-weight:700;color:var(--orange)}
.brand .mark{width:22px;height:22px;background:var(--orange)}
.nav{left:424px;top:56px;display:flex;gap:12px;font-size:10.5px;color:#555;white-space:nowrap}
.nav .active{color:var(--orange)}
.rule{left:0;top:88px;width:850px;height:2px;background:var(--orange)}

/* hero */
.hero{left:0;top:90px;width:850px;height:446px;background:linear-gradient(90deg,var(--olive) 0%,var(--olive-light) 100%)}
.hero-art{left:0;top:110px;width:390px;height:360px;background:linear-gradient(180deg,#d9cc8a,#8d7620)}
.h-kicker{left:421px;top:141px;font-family:"Archivo Black",sans-serif;font-size:27px;color:var(--olive-dark);line-height:1}
.h-title{left:419px;top:162px;font-family:"Archivo Black",sans-serif;font-size:62px;color:var(--olive-dark);line-height:0.86}
.h-copy{left:421px;top:305px;width:360px;font-family:"Arimo",sans-serif;font-size:12.4px;color:var(--white);line-height:1.3}
.platforms{left:421px;top:382px;font-family:"Arimo",sans-serif;font-size:12.4px;color:var(--white)}
.platforms b{margin-right:12px;font-size:13px}
.platform-marks{left:424px;top:428px;display:flex;gap:22px}
.platform-marks span{width:26px;height:26px;border-radius:50%;background:var(--olive-dark);opacity:.7}
.arrow{width:46px;height:46px;border-radius:50%;background:rgba(255,255,255,.6)}
.arrow svg{display:block}
.quote{left:565px;top:490px;width:212px;height:30px;background:rgba(120,100,20,.35);color:var(--white);font-size:17px;padding:4px 0 0 47px}
.quote i{position:absolute;left:4px;top:-20px;width:36px;height:44px;background:#f4efd6;transform:rotate(-12deg)}
.login{left:15px;top:472px;width:226px;height:64px;background:var(--orange);font-size:10px;color:var(--white);padding:6px}
.login .row{display:flex;align-items:center;margin-bottom:5px}
.login label{width:48px}
.login .field{width:160px;height:13px;background:var(--orange-soft);font-size:7px;padding:2px 4px}
.login .foot{font-size:8px;padding-left:84px}
.pager{left:355px;top:515px;width:140px;height:21px;background:var(--orange);display:flex;gap:9px;justify-content:center;align-items:center}
.pager span{width:11px;height:11px;border-radius:50%;background:var(--white)}
.pager span:first-child{background:var(--black)}

/* about */
.about-title{left:10px;top:543px;font-size:17px;font-weight:700;color:var(--orange)}
.about-text{left:8px;top:566px;width:523px;font-size:9.3px;line-height:1.52;text-align:justify}
.about-text p{margin-bottom:14px}
.diagram{left:582px;top:550px;width:256px;height:206px;background:radial-gradient(circle at 50% 50%,#dfe9d4 0%,#f4f6f2 70%)}

/* cards */
.card{top:797px;width:213px;height:215px;border:1px solid #eee;box-shadow:0 0 3px rgba(0,0,0,.08);text-align:center}
.card h3{margin-top:4px;font-size:13.6px;font-weight:700;color:var(--orange)}
.card .art{margin:13px auto 0;width:160px;height:100px;background:linear-gradient(180deg,#eef0f2,#9aa3ab)}
.card p{margin:20px 5px 0;font-size:8.8px;line-height:1.6;text-align:justify}
.card .cta{display:flex;justify-content:space-between;align-items:center;margin:5px 15px 0;font-size:10px;color:var(--orange)}
.card .more{background:var(--orange);color:var(--white);padding:2px 12px;font-size:10px;border-radius:1px}

/* promo band */
.band{left:0;top:1020px;width:850px;height:66px;background:var(--orange)}
.band-logo{left:180px;top:1020px;width:177px;height:66px;background:var(--white);padding:14px 0 0 8px}
.band-logo .name{display:flex;align-items:center;gap:5px;font-size:13px;font-weight:700;color:var(--orange);white-space:nowrap}
.band-logo .name i{width:14px;height:14px;background:var(--orange);flex:none}
.band-logo .tag{margin-top:14px;font-size:6px;letter-spacing:3.5px;color:var(--orange);white-space:nowrap}
.band-copy{left:368px;top:1026px;color:var(--white);font-size:9.5px;line-height:1.5}
.band-copy h4{font-size:12.5px;font-weight:600}
.band-copy b{font-weight:700}

/* partners + footer */
.footer{left:0;top:1086px;width:850px;height:114px;background:var(--black)}
.partners{left:82px;top:1087px;width:686px;height:29px;background:var(--white);display:flex;justify-content:space-around;align-items:center;font-size:10px;font-weight:700;color:var(--orange)}
.foot-nav{left:0;top:1130px;width:850px;text-align:center;font-size:10px;color:var(--white)}
.foot-social{left:398px;top:1153px;display:flex;gap:3px}
.foot-social span{width:16px;height:16px;border-radius:50%;background:var(--orange-soft)}
.copyright{left:0;top:1177px;width:850px;text-align:center;font-size:6.5px;color:var(--white)}
</style>
</head>
<body>

<div class="abs topbar">
  <div class="abs links">Customer Login &nbsp;|&nbsp; Partner Login &nbsp;|&nbsp; Registration</div>
  <div class="abs mail"><i></i>Join our Mailing List</div>
  <div class="abs search">Search</div>
  <div class="abs social"><span class="dot"></span><span class="dot b"></span><span class="dot c"></span></div>
</div>

<div class="abs brand"><span class="mark"></span>Trevantix</div>
<nav class="abs nav">
  <span class="active">Home</span><span>Company</span><span>Products</span><span>Industry</span><span>Partner</span><span>Newsroom</span><span>Blog</span><span>Contact</span>
</nav>
<div class="abs rule"></div>

<section class="abs hero"></section>
<div class="abs hero-art" role="img" aria-label="Three smartphones showing sample mobile apps"></div>
<div class="abs h-kicker">GET YOUR</div>
<div class="abs h-title">MOBILE<br>APPs</div>
<p class="abs h-copy">We offer customizedMobile application development services and marketing solutions to our clients from diverse industries. We strive to deliver affordable Mobile Applications that are unique and user friendly, based solely on your requirements.</p>
<div class="abs platforms">Mobile Apps developed for all the Major mobile Platforms:<br><b>&nbsp;Aplix</b><b>Verdroid</b><b>Mulberrix</b><b>Fernleaf</b><b>Panes Mobile</b></div>
<div class="abs platform-marks"><span></span><span></span><span></span><span></span><span></span></div>
<div class="abs arrow" style="left:10px;top:290px"><svg width="46" height="46"><path d="M27 14 L17 23 L27 32Z" fill="#fff"/></svg></div>
<div class="abs arrow" style="left:776px;top:290px"><svg width="46" height="46"><path d="M19 14 L29 23 L19 32Z" fill="#fff"/></svg></div>
<div class="abs quote"><i></i>REQUEST A <b>QUOTE</b></div>
<form class="abs login">
  <div class="row"><label>User ID</label><div class="field">Username / Email</div></div>
  <div class="row"><label>Password</label><div class="field">Password</div></div>
  <div class="foot"><b>Login</b> | Forget your Password</div>
</form>
<div class="abs pager"><span></span><span></span><span></span><span></span></div>

<h2 class="abs about-title">About Us</h2>
<div class="abs about-text">
  <p>Mit trevantix-example.net kannst du deinen Sport festhalten, auswerten, teilen, dich motivieren und coachen lassen. Nutze einfach deine Lieblings-App, deinen bevorzugten Sportcomputer oder trage manuell ein. Trevantix begleitet, fördert und motiviert dich dein gesamtes Sportlerleben.</p>
  <p>Mit trevantix-example.net<br>&nbsp;kannst du deinen Sport festhalten, auswerten, teilen, dich motivieren und coachen lassen. Nutze einfach deine Lieblings-App, deinen bevorzugten Sportcomputer oder trage manuell ein. Trevantix begleitet, fördert und motiviert dich dein gesamtes Sportlerleben.</p>
  <p>Mit trevantix-example.net kannst du deinen Sport festhalten, auswerten, teilen, dich motivieren und coachen lassen. Nutze einfach deine Lieblings-App, deinen bevorzugten Sportcomputer oder trage manuell ein. Trevantix begleitet, fördert und motiviert dich dein gesamtes Sportlerleben.</p>
</div>

<div class="abs diagram" role="img" aria-label="Illustration of a phone at the centre with arrows to mobile app types: data connectivity, games, embedded software, rich API apps, media apps, utility apps, outlook managers"></div>

<article class="abs card" style="left:84px">
  <h3>Frontend Web Solution</h3>
  <div class="art" role="img" aria-label="Stack of website page layouts"></div>
  <p>Mit trevantix-example.net kannst du deinen Sport festhalten, auswerten, teilen, dich motivieren und coachen lassen.</p>
  <div class="cta"><span>Starting From $200</span><span class="more">Know More ▸</span></div>
</article>
<article class="abs card" style="left:319px">
  <h3>Backend Services</h3>
  <div class="art" role="img" aria-label="Desktop monitor showing a dashboard"></div>
  <p>Mit trevantix-example.net kannst du deinen Sport festhalten, auswerten, teilen, dich motivieren und coachen lassen.</p>
  <div class="cta"><span>Starting From $200</span><span class="more">Know More ▸</span></div>
</article>
<article class="abs card" style="left:553px">
  <h3>Mobile Apps</h3>
  <div class="art" role="img" aria-label="Tablet and phones showing mobile apps"></div>
  <p>Mit trevantix-example.net kannst du deinen Sport festhalten, auswerten, teilen, dich motivieren und coachen lassen.</p>
  <div class="cta"><span>Starting From $200</span><span class="more">Know More ▸</span></div>
</article>

<section class="abs band"></section>
<div class="abs band-logo">
  <div class="name"><i></i>trevantix-example.net</div>
  <div class="tag">OPTIMIZE YOUR SPORT</div>
</div>
<div class="abs band-copy">
  <h4>Mit trevantix-example.net kannst du deinen Sport festhalten,</h4>
  Auswerten, teilen, dich motivieren und coachen lassen.<br>
  Nutze einfach deine<br>
  <b>Visit The Site ▸</b>
</div>

<footer class="abs footer"></footer>
<div class="abs partners">
  <span>Kestrel</span><span>Bolvane</span><span>Velocisport</span><span>Lumera</span><span>Kasuta</span><span>Weighlo</span><span>Yipfit</span><span>PWR</span><span>TrailLedger</span><span>Vantor</span><span>Rollix</span><span>Rowmark</span>
</div>
<div class="abs foot-nav">Home | Company | Products | Industry | Partner | Newsroom | Blog | Contact</div>
<div class="abs foot-social"><span></span><span></span><span></span></div>
<div class="abs copyright">(c) copyright trevantix-example.net. All Right Reserve</div>

</body>
</html>
```